Emergency and Referral Vet Hospital promotional sticker design

We're looking at getting some stickers designed that we could give to clients to put on their cars for promotion and advertising. If they could also be suitable for a goodie bag for conference too that would be great. I like the look of water-colour backgrounds, we'll need to include our logo and probably our address (Unit 3/215 Korrinup Road Tallowmere). We also have a hospital motto "... because they're family" if that could somehow be integrated, we only care for small animals (dogs, cats etc) but the design is very open to suggestion. Would love to see what you can create.

Industry/Entity Type

Veterinary

Colors
0054AA
0677BA
7BADD7
CADEEF
E8F1F8
0094D4
00A9DD
6FCCEA
C7EBF8
E9F6FB

Requirements
Nice to have
• Think beach vibes, blues maybe paw print shapes etc

```html
<!DOCTYPE html>
<html lang="en">
<head>
<meta charset="utf-8">
<title>Tidewell Vet Hospital – Because They're Family</title>
<link href="https://fonts.googleapis.com/css2?family=Catamaran:wght@600;700&display=swap" rel="stylesheet">
<style>
  :root {
    --navy-deep: #0a1a6b;
    --navy: #0b2f9e;
    --royal: #0a4fd8;
    --sky-text: #c7ebf8;
    --paw-light: #c7ebf8;
    --paw-mid: #6fccea;
    --white: #ffffff;
    --photo-teal: #336f80;
    --photo-cream: #e6e1d9;
    --photo-scrub: #5fbcd3;
  }
  html, body {
    margin: 0;
    padding: 0;
    overflow: hidden;
    background: #ffffff;
  }
  .sticker {
    position: relative;
    width: 1200px;
    height: 800px;
    overflow: hidden;
    font-family: "Catamaran", "Helvetica Neue", Arial, sans-serif;
  }
  .hero-photo {
    position: absolute;
    inset: 0;
    background:
      linear-gradient(100deg, rgba(95,188,211,0) 0%, rgba(95,188,211,0) 50%, rgba(95,188,211,0.75) 62%, var(--photo-scrub) 78%, rgba(95,188,211,0.9) 100%) 0 240px / 100% 560px no-repeat,
      linear-gradient(180deg, var(--photo-teal) 0%, #3a7786 27%, #cfd3cf 31%, var(--photo-cream) 36%, #ddd7ce 75%, #ece8e2 100%);
  }
  .brand-panel {
    position: absolute;
    inset: 0;
    background: linear-gradient(115deg, var(--navy-deep) 0%, var(--navy) 45%, var(--royal) 100%);
    clip-path: path('M0 0 H658 C598 180 520 470 508 800 H0 Z');
  }
  .texture-field {
    position: absolute;
    left: 0;
    top: 380px;
    width: 520px;
    height: 420px;
    background: radial-gradient(ellipse 420px 300px at 0 420px, rgba(0,148,212,0.32) 0%, rgba(0,148,212,0.12) 55%, rgba(0,148,212,0) 100%);
  }
  .paw {
    position: absolute;
  }
  .paw-large { left: 448px; top: 70px; width: 62px; height: 62px; transform: rotate(12deg); }
  .paw-medium { left: 390px; top: 197px; width: 62px; height: 62px; transform: rotate(14deg); }
  .paw-small { left: 476px; top: 180px; width: 36px; height: 36px; transform: rotate(18deg); }
  .brand-name {
    position: absolute;
    left: 56px;
    top: 228px;
    margin: 0;
    display: flex;
    align-items: center;
    gap: 12px;
    font-size: 42px;
    font-weight: 700;
    color: var(--white);
    line-height: 1;
    letter-spacing: 0.5px;
  }
  .brand-dot {
    width: 16px;
    height: 16px;
    border-radius: 50%;
    background: var(--white);
  }
  .motto {
    position: absolute;
    left: 55px;
    top: 306px;
    margin: 0;
    font-size: 49px;
    font-weight: 700;
    line-height: 83px;
    color: var(--sky-text);
    letter-spacing: 1px;
    text-transform: uppercase;
  }
  .divider {
    position: absolute;
    left: 50px;
    top: 571px;
    width: 407px;
    height: 1px;
    background: rgba(255,255,255,0.85);
  }
  .address {
    position: absolute;
    left: 50px;
    top: 634px;
    display: flex;
    gap: 13px;
    color: var(--white);
  }
  .address-pin {
    width: 25px;
    height: 34px;
    margin-top: 10px;
    flex: none;
  }
  .address-text {
    margin: 0;
    font-style: normal;
    font-size: 26px;
    font-weight: 600;
    line-height: 50px;
    text-transform: uppercase;
    letter-spacing: 0.4px;
  }
</style>
</head>
<body>
  <main class="sticker">
    <div class="hero-photo" role="img" aria-label="Photo of a smiling veterinary nurse in blue scrubs and a hair cap holding a small white fluffy dog in a clinic"></div>

    <section class="brand-panel">
      <div class="texture-field" role="img" aria-label="Faint scattered diamond texture fading in from the lower left"></div>

      <svg class="paw paw-large" viewBox="0 0 60 60" aria-hidden="true">
        <defs>
          <linearGradient id="pawFill" x1="0" y1="0" x2="1" y2="1">
            <stop offset="0" stop-color="#c7ebf8"/>
            <stop offset="1" stop-color="#6fccea"/>
          </linearGradient>
        </defs>
        <path d="M30 30c8 0 16 9 16 16 0 6-5 8-9 7-3-1-5-2-7-2s-4 1-7 2c-4 1-9-1-9-7 0-7 8-16 16-16z" fill="url(#pawFill)"/>
        <ellipse cx="9" cy="27" rx="6" ry="8" transform="rotate(-25 9 27)" fill="url(#pawFill)"/>
        <ellipse cx="21" cy="12" rx="6" ry="9" transform="rotate(-8 21 12)" fill="url(#pawFill)"/>
        <ellipse cx="39" cy="12" rx="6" ry="9" transform="rotate(8 39 12)" fill="url(#pawFill)"/>
        <ellipse cx="51" cy="27" rx="6" ry="8" transform="rotate(25 51 27)" fill="url(#pawFill)"/>
      </svg>
      <svg class="paw paw-medium" viewBox="0 0 60 60" aria-hidden="true">
        <path d="M30 30c8 0 16 9 16 16 0 6-5 8-9 7-3-1-5-2-7-2s-4 1-7 2c-4 1-9-1-9-7 0-7 8-16 16-16z" fill="url(#pawFill)"/>
        <ellipse cx="9" cy="27" rx="6" ry="8" transform="rotate(-25 9 27)" fill="url(#pawFill)"/>
        <ellipse cx="21" cy="12" rx="6" ry="9" transform="rotate(-8 21 12)" fill="url(#pawFill)"/>
        <ellipse cx="39" cy="12" rx="6" ry="9" transform="rotate(8 39 12)" fill="url(#pawFill)"/>
        <ellipse cx="51" cy="27" rx="6" ry="8" transform="rotate(25 51 27)" fill="url(#pawFill)"/>
      </svg>
      <svg class="paw paw-small" viewBox="0 0 60 60" aria-hidden="true">
        <path d="M30 30c8 0 16 9 16 16 0 6-5 8-9 7-3-1-5-2-7-2s-4 1-7 2c-4 1-9-1-9-7 0-7 8-16 16-16z" fill="url(#pawFill)"/>
        <ellipse cx="9" cy="27" rx="6" ry="8" transform="rotate(-25 9 27)" fill="url(#pawFill)"/>
        <ellipse cx="21" cy="12" rx="6" ry="9" transform="rotate(-8 21 12)" fill="url(#pawFill)"/>
        <ellipse cx="39" cy="12" rx="6" ry="9" transform="rotate(8 39 12)" fill="url(#pawFill)"/>
        <ellipse cx="51" cy="27" rx="6" ry="8" transform="rotate(25 51 27)" fill="url(#pawFill)"/>
      </svg>

      <p class="brand-name"><span class="brand-dot"></span>tidewell</p>

      <h1 class="motto">Because they&#39;re<br>family</h1>

      <div class="divider"></div>

      <div class="address">
        <svg class="address-pin" viewBox="0 0 24 34" aria-hidden="true">
          <path d="M12 1C5.9 1 1 5.8 1 11.8 1 19.5 12 33 12 33s11-13.5 11-21.2C23 5.8 18.1 1 12 1z" fill="#ffffff"/>
          <circle cx="12" cy="12" r="4.3" fill="#0b2f9e"/>
        </svg>
        <address class="address-text">Unit 3/215 Korrinup Road<br>Tallowmere</address>
      </div>
    </section>
  </main>
</body>
</html>
```